Healthcare and Professional IT Services Company need a redesigned business card

We are a IT Services company that targets small medical practices and professional business such as Attorneys, Accounts, Architects etc. We want to communicate a professional yet friendly image using recent logo redesign here on ArtHarbor. Like to see the colors blue and orange in the design. Must use the Tall Pine Computing as displayed in the new logo - then also want to incorporate the fish logo as well.

Target Market(s)

Small medical and professional services

Industry/Entity Type

It Company

Contact Information for Business Card

The usual stuff, place for name address phone website. Also maybe our tagline which is "hooked on technology"

Requirements
Must have
• My new logo and the fish somewhere on the card

```html
<!DOCTYPE html>
<html lang="en">
<head>
<meta charset="utf-8">
<title>Tall Pine Computing – Business Card</title>
<link href="https://fonts.googleapis.com/css2?family=Open+Sans:wght@400;600&display=swap" rel="stylesheet">
<style>
  :root {
    --page-bg: #e6e6e6;
    --card-bg: #f4f4f4;
    --card-edge: #dcdcdc;
    --brand-blue: #1b72b5;
    --name-blue: #3d5fa3;
    --divider-blue: #2b76bd;
    --accent-orange: #e08a2a;
    --ink: #161616;
    --icon-bg: #111111;
    --icon-fg: #ffffff;
  }
  * { box-sizing: border-box; margin: 0; padding: 0; }
  html, body {
    width: 1189px;
    height: 1200px;
    overflow: hidden;
    background: var(--page-bg);
    font-family: "Open Sans", Arial, sans-serif;
  }
  .card {
    position: absolute;
    left: 140px;
    width: 917px;
    height: 523px;
    background: radial-gradient(ellipse at 50% 60%, #fbfbfb 0%, var(--card-bg) 55%, var(--card-edge) 100%);
    box-shadow: 0 3px 8px rgba(0,0,0,0.25);
  }
  .card--front { top: 46px; }
  .card--back { top: 623px; }

  .brand {
    position: absolute;
    display: flex;
    flex-direction: column;
    align-items: center;
    text-align: center;
  }
  .brand__dot {
    border-radius: 50%;
    background: var(--accent-orange);
  }
  .brand__name {
    color: var(--brand-blue);
    font-weight: 600;
    line-height: 1.05;
  }
  .card--front .brand { left: 0; width: 426px; top: 150px; }
  .card--front .brand__dot { width: 56px; height: 56px; margin-bottom: 26px; }
  .card--front .brand__name { font-size: 44px; }

  .card--back .brand { left: 0; width: 917px; top: 150px; }
  .card--back .brand__dot { width: 70px; height: 70px; margin-bottom: 32px; }
  .card--back .brand__name { font-size: 56px; }

  .divider {
    position: absolute;
    left: 426px;
    top: 60px;
    width: 3px;
    height: 414px;
    background: var(--divider-blue);
  }
  .person-name {
    position: absolute;
    left: 472px;
    top: 100px;
    font-size: 41px;
    font-weight: 400;
    color: var(--name-blue);
    letter-spacing: 0.3px;
  }
  .contact-list {
    position: absolute;
    left: 472px;
    top: 356px;
    list-style: none;
  }
  .contact-list__item {
    display: flex;
    align-items: center;
    height: 33px;
    font-size: 24px;
    color: var(--ink);
  }
  .contact-list__icon {
    width: 20px;
    height: 20px;
    margin-right: 24px;
    flex: none;
  }
</style>
</head>
<body>

<section class="card card--front">
  <div class="brand">
    <div class="brand__dot"></div>
    <div class="brand__name">Tall Pine<br>Computing</div>
  </div>

  <div class="divider"></div>

  <h1 class="person-name">Martin Keller</h1>

  <ul class="contact-list">
    <li class="contact-list__item">
      <svg class="contact-list__icon" viewBox="0 0 20 20" aria-hidden="true">
        <rect width="20" height="20" fill="var(--icon-bg)"/>
        <path d="M6 4 L8.5 4 L9.5 7 L8 8.3 Q9.5 11.5 12 12.5 L13.3 11 L16 12 L16 14.5 Q15 16 13 15.6 Q6.5 13.5 4.5 7 Q4.3 5 6 4 Z" fill="var(--icon-fg)"/>
      </svg>
      +1 555 014 2290
    </li>
    <li class="contact-list__item">
      <svg class="contact-list__icon" viewBox="0 0 20 20" aria-hidden="true">
        <rect width="20" height="20" fill="var(--icon-bg)"/>
        <circle cx="10" cy="10" r="6" fill="none" stroke="var(--icon-fg)" stroke-width="1.6"/>
        <path d="M4 10 H16 M10 4 Q6.5 10 10 16 M10 4 Q13.5 10 10 16" fill="none" stroke="var(--icon-fg)" stroke-width="1.2"/>
      </svg>
      www.tallpinecomputing.com
    </li>
    <li class="contact-list__item">
      <svg class="contact-list__icon" viewBox="0 0 20 20" aria-hidden="true">
        <rect width="20" height="20" fill="var(--icon-bg)"/>
        <path d="M10 16.5 Q5 10.5 5 8 A5 5 0 0 1 15 8 Q15 10.5 10 16.5 Z" fill="var(--icon-fg)"/>
        <circle cx="10" cy="8" r="1.8" fill="var(--icon-bg)"/>
      </svg>
      4821 Cedar Row, Maple Bay, BC
    </li>
  </ul>
</section>

<section class="card card--back">
  <div class="brand">
    <div class="brand__dot"></div>
    <div class="brand__name">Tall Pine<br>Computing</div>
  </div>
</section>

</body>
</html>
```